Verdana Crest New Website - Online Learning and Education

New Wordpress website for an online learning site that has courses, worksheets, quizzes, etc.
Updates

We would like something similar to this website: https://hallowaybridgeinstitute.example/mediation-skills-course/. But continue with the content of our current website: http://verdanacrestlearninghub.example

We would like something similar to this site: https://hallowaybridgeinstitute.example/mediation-skills-course/

Coding

Coded - Design and coding required

```html
<!DOCTYPE html>
<html lang="en">
<head>
<meta charset="utf-8">
<title>Verdana Crest Learning System</title>
<link rel="stylesheet" href="https://fonts.googleapis.com/css2?family=Open+Sans:wght@400;600;700&family=Poppins:wght@600;700;800&display=swap">
<style>
:root{
  --red:#be1e2d;
  --navy:#0d3b78;
  --navy-dark:#0a2f63;
  --footer:#24538f;
  --ink:#1c1c1c;
  --body:#3d3d3d;
  --white:#ffffff;
  --rule:#5d80b0;
}
*{margin:0;padding:0;box-sizing:border-box}
html,body{width:1200px;height:3591px;overflow:hidden;background:var(--white)}
body{font-family:"Open Sans",Arial,sans-serif;color:var(--body)}
.page{position:relative;width:1200px;height:3591px;overflow:hidden}
.abs{position:absolute}

/* header */
.site-header{position:absolute;left:0;top:0;width:1200px;height:111px;background:var(--white)}
.brand{position:absolute;left:140px;top:30px;display:flex;align-items:center;gap:12px}
.brand-dot{width:44px;height:44px;border-radius:50%;background:var(--navy)}
.brand-name{font-family:"Poppins",sans-serif;font-weight:600;font-size:32px;color:var(--navy);letter-spacing:.5px}
.follow{position:absolute;left:833px;top:28px;display:flex;align-items:center;gap:8px;font-size:12px;font-weight:600;color:var(--ink)}
.follow .dot{width:26px;height:26px;border-radius:50%;background:var(--navy)}
.follow .dot.mid{background:#1da1f2}
.search{position:absolute;left:1032px;top:30px}
.main-nav{position:absolute;top:77px;left:0;width:1200px;font-size:13px;font-weight:700;color:var(--ink)}
.main-nav span{position:absolute;white-space:nowrap}
.main-nav .active{color:var(--red)}

/* hero */
.hero{position:absolute;left:0;top:111px;width:1200px;height:551px;background:linear-gradient(90deg,#eef1f3 0%,#e2e7ea 45%,#c9d3d8 70%,#a9bac6 100%)}
.hero-title{position:absolute;left:149px;top:272px;font-family:"Poppins",sans-serif;font-weight:800;font-size:36px;color:#111;letter-spacing:-1px;white-space:nowrap}
.hero-sub{position:absolute;left:149px;top:325px;font-size:21px;color:#222}
.btn-red{position:absolute;background:var(--red);color:var(--white);font-family:"Poppins",sans-serif;font-weight:700;display:flex;align-items:center;justify-content:center;text-align:center}
.hero-btn{left:152px;top:376px;width:178px;height:51px;font-size:19px}

/* welcome */
.welcome-mark{position:absolute;left:92px;top:696px;width:86px;height:86px;border-radius:50%;background:var(--navy)}
.welcome-kicker{position:absolute;left:190px;top:700px;font-size:27px;color:var(--ink);font-weight:400}
.welcome-name{position:absolute;left:189px;top:728px;font-family:"Poppins",sans-serif;font-weight:800;font-size:44px;color:var(--navy);line-height:1}
.copy{position:absolute;left:128px;width:548px;font-size:17.5px;line-height:24px;color:var(--body)}
.checklist{position:absolute;left:130px;top:1094px;list-style:none;font-size:17.5px;color:var(--ink)}
.checklist li{display:flex;align-items:center;gap:12px;height:38.4px}
.read-more{left:131px;top:1386px;width:144px;height:41px;font-size:15px}

/* accordion */
.course-toggle{position:absolute;left:130px;top:1471px;width:528px;height:63px;border:2px solid var(--red);display:flex;align-items:center;justify-content:space-between;padding:0 22px;font-family:"Poppins",sans-serif;font-weight:700;font-size:22px;color:var(--red)}
.accordion{position:absolute;left:129px;top:1560px;width:529px}
.accordion-row{height:38px;margin-bottom:6.6px;background:var(--navy);color:var(--white);font-size:15px;font-weight:600;display:flex;align-items:center;justify-content:space-between;padding:0 18px}
.plus{font-size:22px;font-weight:700;line-height:1}

/* content sections */
.section-title{position:absolute;left:129px;font-family:"Open Sans",sans-serif;font-weight:700;font-size:27px;color:var(--ink)}
.screen{position:absolute;left:134px;width:322px;background:linear-gradient(180deg,#e4e6ea 0%,#f6f6f6 20%,#ededed 100%);border-left:4px solid #333;border-right:4px solid #333}
.video{position:absolute;left:128px;top:2835px;width:559px;height:322px;background:linear-gradient(120deg,#9aa3ad 0%,#c3c8cc 45%,#8e8a84 100%)}
.play{position:absolute;left:249px;top:132px;width:60px;height:60px;border-radius:50%;background:rgba(255,255,255,.9)}

/* sidebar */
.cta-box{left:739px;width:329px;height:96px;font-size:22px;line-height:30px}
.cta-box.small{font-size:20px;line-height:29px}
.side-heading{position:absolute;left:739px;width:329px;text-align:center;font-size:22px;font-weight:600;color:var(--ink)}
.course-title{position:absolute;left:739px;width:320px;text-align:center;font-size:17px;color:var(--ink)}
.btn-outline{position:absolute;left:839px;width:116px;height:33px;border:2px solid var(--navy);color:var(--navy);font-size:14px;font-weight:600;display:flex;align-items:center;justify-content:center}
.recent-title{position:absolute;left:738px;top:1470px;font-size:23px;color:var(--ink)}
.post{position:absolute;left:742px;width:310px;display:flex;gap:14px;font-size:17.5px;line-height:21px;font-weight:600;color:var(--navy)}
.post svg{flex:none;margin-top:5px}

/* footer */
.site-footer{position:absolute;left:0;top:3196px;width:1200px;height:395px;background:var(--footer);color:var(--white)}
.footer-brand{position:absolute;left:130px;top:135px;display:flex;align-items:center;gap:12px}
.footer-brand .disc{width:56px;height:56px;border-radius:50%;background:var(--white)}
.footer-brand span{font-family:"Poppins",sans-serif;font-weight:600;font-size:28px}
.f-head{position:absolute;top:58px;font-size:12px;font-weight:700}
.f-text{position:absolute;font-size:13.5px;line-height:19px}
.f-list{position:absolute;left:716px;top:90px;list-style:none;font-size:13.5px;line-height:24px}
.f-social{position:absolute;left:935px;display:flex;align-items:center;gap:10px;font-size:12px}
.f-social .disc{width:26px;height:26px;border-radius:50%;background:var(--white);opacity:.9}
.f-rule{position:absolute;left:406px;top:292px;width:640px;height:1px;background:var(--rule)}
.copyright{position:absolute;right:153px;top:338px;font-size:12px}
</style>
</head>
<body>
<div class="page">

  <header class="site-header">
    <div class="brand"><div class="brand-dot"></div><div class="brand-name">VERDANA CREST</div></div>
    <div class="follow">FOLLOW US <span class="dot"></span><span class="dot mid"></span><span class="dot"></span></div>
    <svg class="search" width="20" height="20" viewBox="0 0 20 20"><circle cx="8" cy="8" r="6" fill="none" stroke="#444" stroke-width="2.4"/><line x1="12.5" y1="12.5" x2="18" y2="18" stroke="#444" stroke-width="2.6"/></svg>
    <nav class="main-nav">
      <span class="active" style="left:553px">HOME</span>
      <span style="left:624px">ABOUT US</span>
      <span style="left:725px">FEATURES</span>
      <span style="left:820px">PRICING</span>
      <span style="left:909px">BLOG</span>
      <span style="left:976px">CONTACT US</span>
    </nav>
  </header>

  <section class="hero" role="img" aria-label="Photo of a smiling student wearing headphones at a laptop in a bright office with a plant"></section>
  <h1 class="hero-title">VERDANA CREST LEARNING SYSTEM</h1>
  <p class="hero-sub">Get Your Bearings. Plan Your Course.</p>
  <a class="btn-red hero-btn">GET STARTED</a>

  <div class="welcome-mark"></div>
  <div class="welcome-kicker">WELCOME TO</div>
  <div class="welcome-name">VERDANA CREST</div>
  <p class="copy" style="top:804px">Verdana Crest is an online learning application geared toward corporate customers, allowing their employees to identify and cultivate new skills that will be valuable in both their professional and personal lives. Like a trusted guide on a long trail, Verdana Crest can help your people get their bearings for where they’re headed, and then help them plan a course to get there.</p>
  <p class="copy" style="top:995px">Concentrating on subjects that are useful to each student not only in the business world but also in life as well, our program offers courses on various topics including:</p>
  <ul class="checklist">
    <li><svg width="16" height="14" viewBox="0 0 16 14"><path d="M1 7l5 5 9-10" fill="none" stroke="#be1e2d" stroke-width="3.2"/></svg>Become a Better Listener</li>
    <li><svg width="16" height="14" viewBox="0 0 16 14"><path d="M1 7l5 5 9-10" fill="none" stroke="#be1e2d" stroke-width="3.2"/></svg>Proactive Decision-Making</li>
    <li><svg width="16" height="14" viewBox="0 0 16 14"><path d="M1 7l5 5 9-10" fill="none" stroke="#be1e2d" stroke-width="3.2"/></svg>Improving Self-Awareness</li>
    <li><svg width="16" height="14" viewBox="0 0 16 14"><path d="M1 7l5 5 9-10" fill="none" stroke="#be1e2d" stroke-width="3.2"/></svg>The Power of Priorities</li>
    <li><svg width="16" height="14" viewBox="0 0 16 14"><path d="M1 7l5 5 9-10" fill="none" stroke="#be1e2d" stroke-width="3.2"/></svg>Mastering Habits</li>
    <li><svg width="16" height="14" viewBox="0 0 16 14"><path d="M1 7l5 5 9-10" fill="none" stroke="#be1e2d" stroke-width="3.2"/></svg>Managing a To-Do List</li>
    <li><svg width="16" height="14" viewBox="0 0 16 14"><path d="M1 7l5 5 9-10" fill="none" stroke="#be1e2d" stroke-width="3.2"/></svg>Perfection: The Enemy of Progress</li>
  </ul>
  <a class="btn-red read-more">READ MORE</a>

  <div class="course-toggle"><span>TAKE THE FULL COURSE NOW</span><span class="plus">+</span></div>
  <div class="accordion">
    <div class="accordion-row"><span>Lorem Ipsum is simply dummy text of the printing</span><span class="plus">+</span></div>
    <div class="accordion-row"><span>Contrary to popular belief korem</span><span class="plus">+</span></div>
    <div class="accordion-row"><span>The standard chunk of Lorem Ipsum used</span><span class="plus">+</span></div>
    <div class="accordion-row"><span>There are many variations of passages</span><span class="plus">+</span></div>
    <div class="accordion-row"><span>Sed ut perspiciatis unde omnis iste natus error</span><span class="plus">+</span></div>
    <div class="accordion-row"><span>Lorem Ipsum is simply dummy text of the printing</span><span class="plus">+</span></div>
  </div>

  <h2 class="section-title" style="top:1866px">Different Learning Styles</h2>
  <p class="copy" style="left:131px;width:560px;top:1920px">Verdana Crest realizes that different people learn in different ways, so we strive to accommodate that. Our courses include various methods of information dissemination in order to allow for different learning styles: some reading, some video, some reflections, some group activities, and some journaling. Each course includes a brief quiz to ensure you’ve absorbed the important information. And, if your organization chooses to work through these courses together as a group, that will further enhance your team’s learning experience.</p>

  <h2 class="section-title" style="top:2152px">Sample Screens</h2>
  <div class="screen" style="top:2216px;height:249px" role="img" aria-label="Screenshot of a course lesson page with overview text, an image and a course outline sidebar"></div>
  <div class="screen" style="top:2488px;height:247px" role="img" aria-label="Screenshot of a course quiz page with answer options and a progress sidebar"></div>

  <h2 class="section-title" style="top:2785px">Overview video</h2>
  <div class="video" role="img" aria-label="Video still of a man with a headset working on a laptop in an open office">
    <div class="play"></div>
    <svg class="abs" style="left:272px;top:149px" width="20" height="26" viewBox="0 0 20 26"><path d="M2 1l17 12L2 25z" fill="#b5b9bf"/></svg>
  </div>

  <a class="btn-red cta-box" style="top:715px">SAMPLE OUR<br>VERDANA CREST COURSE</a>
  <div class="side-heading" style="top:846px">ONLINE COURSES</div>
  <div class="course-title" style="top:902px">Become a Better Listener</div>
  <a class="btn-outline" style="top:941px">READ MORE</a>
  <div class="course-title" style="top:1005px">Proactive Decision-Making</div>
  <a class="btn-outline" style="top:1044px">READ MORE</a>
  <div class="course-title" style="top:1106px">Improving Self-Awareness</div>
  <a class="btn-outline" style="top:1144px">READ MORE</a>
  <div class="course-title" style="top:1205px">The Power of Priorities</div>
  <a class="btn-outline" style="top:1243px">READ MORE</a>
  <a class="btn-red cta-box small" style="top:1330px">VERDANA CREST RIGHT TO<br>YOUR INBOX. SUBSCRIBE!</a>

  <div class="recent-title">RECENT POSTS</div>
  <div class="post" style="top:1524px"><svg width="8" height="12" viewBox="0 0 8 12"><path d="M1 1l5 5-5 5" fill="none" stroke="#be1e2d" stroke-width="2.4"/></svg><span>But I must explain to you how all</span></div>
  <div class="post" style="top:1563px"><svg width="8" height="12" viewBox="0 0 8 12"><path d="M1 1l5 5-5 5" fill="none" stroke="#be1e2d" stroke-width="2.4"/></svg><span>At vero eos et accusamus et<br>iusto odio dignissimos</span></div>
  <div class="post" style="top:1628px"><svg width="8" height="12" viewBox="0 0 8 12"><path d="M1 1l5 5-5 5" fill="none" stroke="#be1e2d" stroke-width="2.4"/></svg><span>Lorem ipsum dolor sit amet consectetur adipiscin.</span></div>
  <div class="post" style="top:1695px"><svg width="8" height="12" viewBox="0 0 8 12"><path d="M1 1l5 5-5 5" fill="none" stroke="#be1e2d" stroke-width="2.4"/></svg><span>At vero eos et accusamus</span></div>
  <div class="post" style="top:1740px"><svg width="8" height="12" viewBox="0 0 8 12"><path d="M1 1l5 5-5 5" fill="none" stroke="#be1e2d" stroke-width="2.4"/></svg><span>On the other hand, we denounce with righteous indignation</span></div>

  <footer class="site-footer">
    <div class="footer-brand"><div class="disc"></div><span>VERDANA CREST</span></div>

    <div class="f-head" style="left:408px">CONTACT US</div>
    <svg class="abs" style="left:408px;top:95px" width="8" height="11" viewBox="0 0 8 11"><path d="M4 11C1 6 0 5 0 4a4 4 0 018 0c0 1-1 2-4 7z" fill="#fff"/><circle cx="4" cy="4" r="1.5" fill="#24538f"/></svg>
    <div class="f-text" style="left:429px;top:89px">Unit 12, 48 Larkspur Avenue<br>&nbsp;Westbrook 40218</div>
    <svg class="abs" style="left:407px;top:148px" width="11" height="11" viewBox="0 0 11 11"><path d="M2 0l2 3-1 1.5c1 2 2 3 3.5 3.5L8 7l3 2-1 2C5 11 0 6 0 1z" fill="#fff"/></svg>
    <div class="f-text" style="left:429px;top:142px">555.014.2290</div>
    <svg class="abs" style="left:407px;top:184px" width="12" height="9" viewBox="0 0 12 9"><rect width="12" height="9" fill="#fff"/><path d="M0 0l6 5 6-5" fill="none" stroke="#24538f" stroke-width="1.2"/></svg>
    <div class="f-text" style="left:432px;top:178px">info@verdanacrest.example</div>

    <div class="f-head" style="left:716px">MENU</div>
    <ul class="f-list"><li>HOME</li><li>ABOUT US</li><li>FEATURES</li><li>PRICING</li><li>BLOG</li><li>CONTACT US</li></ul>

    <div class="f-head" style="left:933px">CONNECT WITH US</div>
    <div class="f-social" style="top:97px"><span class="disc"></span>Friendlink</div>
    <div class="f-social" style="top:137px"><span class="disc"></span>Chirpline</div>
    <div class="f-social" style="top:176px"><span class="disc"></span>Workweb</div>

    <div class="f-rule"></div>
    <div class="copyright">Copyrights @ 2019 All Rights Reserved</div>
  </footer>

</div>
</body>
</html>
```